Flag Order

We were just looking to order some branding flags to put on our rental equipment for our business. We would like different examples of the colors, shapes, sizes, backgrounds etc. Was thinking of just doing the plains icon instead of the whole logo on there. but open to ideas. preferably not a white background as they could get dirty,

```html
<!DOCTYPE html>
<html lang="en">
<head>
<meta charset="utf-8">
<title>Rampway Banner Flags</title>
<link href="https://fonts.googleapis.com/css2?family=Montserrat:wght@800&display=swap" rel="stylesheet">
<style>
  :root {
    --backdrop: #4f4f4f;
    --flag-white: #ffffff;
    --ink: #2a2a2a;
    --accent-blue: #0a93e6;
    --footer-blue: #438bca;
  }
  html, body {
    margin: 0;
    padding: 0;
    width: 1200px;
    height: 1200px;
    overflow: hidden;
    background: var(--backdrop);
  }
  .canvas {
    position: relative;
    width: 1200px;
    height: 1200px;
    background: var(--backdrop);
  }
  .banner-flag {
    position: absolute;
    top: 276px;
    width: 170px;
    height: 474px;
    box-shadow: 0 0 0 1px rgba(255, 255, 255, 0.12);
  }
  .banner-flag--left {
    left: 334px;
    background: var(--ink);
  }
  .banner-flag--right {
    left: 796px;
    background: var(--accent-blue);
  }
  .banner-flag__corner {
    position: absolute;
    inset: 0;
    width: 170px;
    height: 474px;
  }
  .banner-flag__brand {
    position: absolute;
    left: 0;
    right: 0;
    top: 228px;
    display: flex;
    align-items: center;
    justify-content: center;
    gap: 7px;
  }
  .brand-square {
    width: 11px;
    height: 11px;
  }
  .banner-flag--left .brand-square { background: var(--accent-blue); }
  .banner-flag--right .brand-square { background: var(--ink); }
  .brand-name {
    font-family: "Montserrat", sans-serif;
    font-weight: 800;
    font-size: 19px;
    letter-spacing: 0.5px;
    line-height: 1;
    color: var(--flag-white);
    white-space: nowrap;
  }
  .footer-band {
    position: absolute;
    left: 401px;
    top: 1170px;
    width: 397px;
    height: 30px;
    background: var(--footer-blue);
  }
</style>
</head>
<body>
  <main class="canvas">
    <section class="banner-flag banner-flag--left">
      <svg class="banner-flag__corner" viewBox="0 0 170 474" aria-hidden="true">
        <polygon points="106,474 170,398 170,434 136,474" fill="var(--accent-blue)"/>
        <polygon points="151,474 170,452 170,474" fill="var(--flag-white)"/>
      </svg>
      <div class="banner-flag__brand">
        <span class="brand-square"></span>
        <span class="brand-name">RAMPWAY</span>
      </div>
    </section>

    <section class="banner-flag banner-flag--right">
      <svg class="banner-flag__corner" viewBox="0 0 170 474" aria-hidden="true">
        <polygon points="106,474 170,398 170,434 136,474" fill="var(--ink)"/>
        <polygon points="151,474 170,452 170,474" fill="var(--flag-white)"/>
      </svg>
      <div class="banner-flag__brand">
        <span class="brand-square"></span>
        <span class="brand-name">RAMPWAY</span>
      </div>
    </section>

    <div class="footer-band"></div>
  </main>
</body>
</html>
```